Need Business Card ASAP

We need a business card design for a meeting coming up in a few days. The company name is Harlow Ridge Building and Construction and the logo is attached. Something clean, cool, and contemporary that we can get to a printer right away. Attached is the business card for Volmar Energy, an affiliated company, which we like. Instead of the hawk on the back, you could use the attached "D". We'll also be needing matching letterhead in the near future, so ideas for that are welcome.

```html
<!DOCTYPE html>
<html lang="en">
<head>
<meta charset="utf-8">
<title>Harlow Ridge Building and Construction – Business Card</title>
<link rel="stylesheet" href="https://fonts.googleapis.com/css2?family=Exo+2:wght@400;600&display=swap">
<style>
  :root{
    --bg:#d9d9d6;
    --card-white:#ffffff;
    --card-shade:#ececea;
    --gold:#c3b77d;
    --gold-light:#d6cd9f;
    --gold-deep:#aa9e62;
    --ink:#2a2720;
    --ink-soft:#3d3a31;
    --silver:#a4a4a4;
  }
  *{box-sizing:border-box;margin:0;padding:0}
  html,body{width:1200px;height:1018px;overflow:hidden}
  body{
    background:var(--bg);
    font-family:"Exo 2",sans-serif;
    color:var(--ink);
    position:relative;
  }
  .card{
    position:absolute;
    left:280px;
    width:640px;
    height:366px;
    overflow:hidden;
    box-shadow:0 10px 28px rgba(0,0,0,.22);
  }
  .card--back{top:90px;background:var(--gold)}
  .card--front{top:562px;background:linear-gradient(135deg,var(--card-white) 40%,var(--card-shade))}

  .brand{
    position:absolute;
    display:flex;
    align-items:center;
    gap:10px;
  }
  .brand__mark{
    width:34px;height:34px;
    background:var(--gold-deep);
    flex:none;
  }
  .brand__name{
    font-weight:600;
    font-size:15px;
    line-height:1.2;
    color:var(--ink);
    width:170px;
  }

  .back__panel{
    position:absolute;
    left:0;top:0;
    width:420px;height:100%;
    background:radial-gradient(circle at 40% 40%,#ffffff 50%,var(--card-shade));
    border-radius:0 183px 183px 0;
  }
  .card--back .brand{left:56px;top:60px}
  .back__web{
    position:absolute;
    right:22px;top:40px;bottom:40px;
    width:38px;
    background:var(--card-white);
    display:flex;align-items:center;justify-content:center;
  }
  .back__web span{
    transform:rotate(-90deg);
    white-space:nowrap;
    font-size:14px;
    letter-spacing:.12em;
    color:var(--ink-soft);
  }

  .card--front .brand{left:40px;top:40px}
  .front__panel{
    position:absolute;
    left:300px;top:78px;right:0;bottom:0;
    background:radial-gradient(circle at 30% 35%,var(--gold-light),var(--gold) 55%,var(--gold-deep));
    border-radius:150px 0 0 150px / 150px 0 0 150px;
    border-left:4px solid var(--silver);
    border-top:3px solid var(--silver);
  }
  .person{
    position:absolute;
    right:36px;top:102px;
    text-align:right;
  }
  .person__rule{
    position:absolute;
    right:36px;top:96px;
    width:250px;height:2px;
    background:var(--ink);
  }
  .person__name{font-weight:600;font-size:20px;letter-spacing:.06em}
  .person__role{font-size:14px;letter-spacing:.14em;margin-top:2px}
  .contacts{
    position:absolute;
    right:36px;top:176px;
    list-style:none;
    display:flex;flex-direction:column;gap:8px;
  }
  .contacts li{
    display:flex;align-items:center;justify-content:flex-end;gap:10px;
    font-size:12px;letter-spacing:.05em;
    color:var(--ink);
    white-space:nowrap;
  }
  .contacts svg{width:20px;height:20px;flex:none}
</style>
</head>
<body>

<section class="card card--back" aria-label="Business card back">
  <div class="back__panel"></div>
  <div class="brand">
    <span class="brand__mark"></span>
    <span class="brand__name">Harlow Ridge Building and Construction</span>
  </div>
  <div class="back__web"><span>www.harlowridge.build</span></div>
</section>

<section class="card card--front" aria-label="Business card front">
  <div class="brand">
    <span class="brand__mark"></span>
    <span class="brand__name">Harlow Ridge Building and Construction</span>
  </div>
  <div class="front__panel"></div>
  <div class="person__rule"></div>
  <div class="person">
    <p class="person__name">EVAN MARLOW</p>
    <p class="person__role">GENERAL MANAGER</p>
  </div>
  <ul class="contacts">
    <li>014 552 0378
      <svg viewBox="0 0 20 20"><circle cx="10" cy="10" r="9" fill="none" stroke="#2a2720" stroke-width="1.4"/><path d="M7 5.5l2 2-1.2 1.4a6 6 0 0 0 3.3 3.3l1.4-1.2 2 2-1.3 1.5c-3.5-.3-6.7-3.5-7-7z" fill="#2a2720"/></svg>
    </li>
    <li>014 552 0391
      <svg viewBox="0 0 20 20"><circle cx="10" cy="10" r="9" fill="#2a2720"/><rect x="7" y="4.5" width="6" height="11" rx="1" fill="#c3b77d"/><rect x="8" y="6" width="4" height="7" fill="#2a2720"/></svg>
    </li>
    <li>evan@harlowridge.build
      <svg viewBox="0 0 20 20"><circle cx="10" cy="10" r="9" fill="#2a2720"/><rect x="5" y="6.5" width="10" height="7" fill="#c3b77d"/><path d="M5 6.5l5 4 5-4" fill="none" stroke="#2a2720" stroke-width="1"/></svg>
    </li>
    <li>www.harlowridge.build
      <svg viewBox="0 0 20 20"><circle cx="10" cy="10" r="9" fill="#2a2720"/><circle cx="10" cy="10" r="5" fill="none" stroke="#c3b77d" stroke-width="1.2"/><path d="M5 10h10M10 5c-2.5 3-2.5 7 0 10M10 5c2.5 3 2.5 7 0 10" fill="none" stroke="#c3b77d" stroke-width="1"/></svg>
    </li>
    <li>42 Quarry Lane, 3rd Floor, Eastfield Park
      <svg viewBox="0 0 20 20"><circle cx="10" cy="10" r="9" fill="#2a2720"/><path d="M10 15s-4-4.2-4-7a4 4 0 0 1 8 0c0 2.8-4 7-4 7z" fill="#c3b77d"/><circle cx="10" cy="8" r="1.5" fill="#2a2720"/></svg>
    </li>
  </ul>
</section>

</body>
</html>
```